New business blog needs wordpress theme

I need a unique wordpress theme for my new business oriented blog at hollowpeakdesk.com. The blog focuses on my experience as an entrepreneur and offers insights into business problems while chronicling my experience building a new company.

I would like to see a theme that looks more like a creative professional's website, not a business website. Large photos, bright colors, unique layout. I do not want stock photos of people in suits doing business type things. Also, no pictures of me - I am blogging anonymously.

The design should communicate technology and beauty - for example, I really like the feel of the landing page at www.tundrelo.com - it is beautiful to look at but also reflects the cutting edge nature of what they are doing.

Industry/Entity Type

Business

```html
<!DOCTYPE html>
<html lang="en">
<head>
<meta charset="utf-8">
<title>Hollow Peak – Business Blog</title>
<link rel="stylesheet" href="https://fonts.googleapis.com/css2?family=Open+Sans:wght@300;400;600;700&display=swap">
<style>
:root{
  --sky:#12a3e6;
  --sky-deep:#0a78c2;
  --ink:#1d1f22;
  --nav:#222426;
  --nav-line:#3a3c3f;
  --title-blue:#1b7bc4;
  --panel:#efefef;
  --text:#555;
  --muted:#777;
  --accent-red:#c0392b;
  --btn:#3b3b3b;
  --page-grey:#8a8a8a;
  --footer:#ebebeb;
}
*{box-sizing:border-box;margin:0;padding:0}
html,body{width:1200px;height:2571px;overflow:hidden}
body{position:relative;background:#fff;font-family:"Open Sans",Arial,sans-serif;color:var(--text)}
a{color:inherit;text-decoration:none}

.site-header{position:absolute;left:0;top:0;width:1200px;height:130px;
  background:linear-gradient(180deg,#1cb4f2 0%,var(--sky) 45%,var(--sky-deep) 100%)}
.site-title{position:absolute;top:16px;width:100%;text-align:center;color:#fff;font-size:54px;line-height:70px;font-weight:300;letter-spacing:-.5px}
.site-title strong{font-weight:600}

.main-nav{position:absolute;left:99px;top:106px;width:1002px;height:48px;background:var(--nav);display:flex;align-items:center;z-index:2;box-shadow:0 2px 4px rgba(0,0,0,.3)}
.main-nav a{height:48px;line-height:48px;padding:0 27px;color:#ddd;font-size:14px;text-transform:uppercase;border-right:1px solid var(--nav-line)}
.main-nav a.is-current{background:#141516;color:#fff;font-weight:700;padding:0 31px}
.nav-search{margin-left:auto;margin-right:10px;width:212px;height:30px;background:#fff;border:1px solid #ccc;display:flex;align-items:center;padding:0 8px;font-size:12px;color:#999}
.nav-search svg{margin-left:auto}

.hero{position:absolute;left:0;top:130px;width:1200px;height:501px;
  background:linear-gradient(180deg,#d9d0c4 0%,#e7c39a 35%,#e9a35c 65%,#b96a33 100%)}
.hero-caption{position:absolute;left:0;width:100%;text-align:center}
.hero-caption span{display:inline-block;background:rgba(255,255,255,.72);color:#222;font-size:23px;font-weight:600;text-transform:uppercase;padding:0 34px;line-height:43px}
.hero-caption.line-1{top:204px}
.hero-caption.line-2{top:257px}
.hero-arrow{position:absolute;top:231px;width:40px;height:40px;border-radius:50%;background:rgba(255,255,255,.8);display:flex;align-items:center;justify-content:center}
.hero-arrow.prev{left:28px}
.hero-arrow.next{right:28px}

.post{position:absolute;left:134px;width:932px;background:var(--panel);display:flex}
.post-photo{width:380px;flex:none;height:100%}
.post-body{padding:16px 24px 0 21px}
.post-title{color:var(--title-blue);font-size:22px;line-height:29px;font-weight:600;text-transform:uppercase}
.post-meta{display:inline-block;background:#fff;font-size:11px;color:#555;padding:6px 12px;margin:12px 0 18px;text-transform:uppercase}
.post-meta .comments{color:var(--accent-red);font-weight:600}
.post-body p{font-size:13px;line-height:23px;color:var(--text);margin-bottom:6px}
.read-more{display:inline-block;background:var(--btn);color:#fff;font-size:11px;font-weight:600;text-transform:uppercase;padding:6px 13px;margin-top:12px}

.pagination{position:absolute;top:1920px;left:0;width:1200px;display:flex;justify-content:center;gap:11px}
.pagination span{width:31px;height:31px;line-height:31px;text-align:center;font-size:15px;background:var(--page-grey);color:#fff;border-radius:2px}
.pagination span.is-current{background:#e9e9e9;color:#666}
.pagination span.arrow{background:#e1e1e1;color:#888;font-size:12px}

.divider{position:absolute;left:101px;top:2000px;width:998px;border-top:1px solid #ddd}

.widget{position:absolute;top:2040px;width:312px}
.widget h3{color:var(--title-blue);font-size:25px;font-weight:600;text-transform:uppercase;line-height:32px}
.widget-bar{height:10px;margin-top:4px;background:linear-gradient(90deg,#3a3a3a,#5a5a5a 70%,#9a9a9a)}
.widget ul{list-style:none;background:linear-gradient(180deg,#f2f2f2,#e4e4e4);height:275px;padding:18px 14px 0 14px}
.widget li{position:relative;padding-left:25px;font-size:13px;line-height:21px;color:#555;margin-bottom:13px}
.widget li::before{content:"";position:absolute;left:0;top:4px;width:12px;height:12px;border-radius:50%;background:#bbb}
.widget li::after{content:"";position:absolute;left:4px;top:7px;border-left:5px solid #fff;border-top:3px solid transparent;border-bottom:3px solid transparent}

.newsletter{position:absolute;left:101px;top:2381px;width:998px;height:60px;background:linear-gradient(180deg,#4a4a4a,#2c2c2c);display:flex;align-items:center;padding-left:36px}
.newsletter-label{color:#fff;font-size:23px;margin-left:14px}
.newsletter-field{margin-left:22px;width:265px;height:36px;background:#fff;display:flex;align-items:center;padding:0 8px 0 16px;font-size:12px;color:#888}
.newsletter-field svg{margin-left:auto}
.social-links{margin-left:auto;height:60px;border-left:1px solid #555;display:flex;align-items:center;gap:22px;padding:0 34px 0 38px}
.social-links span{width:32px;height:32px;background:linear-gradient(180deg,#f4f4f4,#c8c8c8);border-radius:3px}

.site-footer{position:absolute;left:0;top:2469px;width:1200px;height:102px;background:var(--footer)}
.footer-nav{position:absolute;left:99px;top:24px;font-size:13px;color:#555}
.footer-nav i{font-style:normal;margin:0 11px}
.copyright{position:absolute;left:99px;top:56px;font-size:13px;color:#555}
.to-top{position:absolute;left:1064px;top:34px;width:36px;height:36px;border-radius:50%;background:#a9a9a9;display:flex;align-items:center;justify-content:center}
</style>
</head>
<body>

<header class="site-header">
  <h1 class="site-title">Hollow <strong>Peak</strong></h1>
</header>

<nav class="main-nav">
  <a class="is-current" href="#">Home</a>
  <a href="#">Small Business</a>
  <a href="#">Technology</a>
  <a href="#">About Elliot</a>
  <a href="#">Contact</a>
  <div class="nav-search">Search
    <svg width="16" height="16" viewBox="0 0 16 16"><circle cx="6.5" cy="6.5" r="4.8" fill="none" stroke="#888" stroke-width="2"/><line x1="10" y1="10" x2="14.5" y2="14.5" stroke="#888" stroke-width="2.4"/></svg>
  </div>
</nav>

<section class="hero" role="img" aria-label="Sunlit city skyline with a tall skyscraper at golden hour">
  <div class="hero-caption line-1"><span>Elliot talks business. Best practices, articles and tips and</span></div>
  <div class="hero-caption line-2"><span>about small business in the United States</span></div>
  <a class="hero-arrow prev" href="#"><svg width="12" height="14" viewBox="0 0 12 14"><path d="M8 2 3 7l5 5" fill="none" stroke="#999" stroke-width="2"/></svg></a>
  <a class="hero-arrow next" href="#"><svg width="12" height="14" viewBox="0 0 12 14"><path d="M4 2l5 5-5 5" fill="none" stroke="#999" stroke-width="2"/></svg></a>
</section>

<article class="post" style="top:665px;height:429px">
  <div class="post-photo" role="img" aria-label="Young man on the floor with a laptop, paper envelopes flying out of the screen" style="background:radial-gradient(circle at 70% 40%,#6f86b3,#2c3d63 60%,#1c2744)"></div>
  <div class="post-body">
    <h2 class="post-title">Comparing Direct Mail to Dealsy – By the Numbers</h2>
    <div class="post-meta">Posted on March 6, 2014 by Elliot &nbsp;—&nbsp; <span class="comments">Leave a comment</span></div>
    <p>Unhappy with the results of a direct mail (snail mail) campaign, I decided to compare the results to a Dealsy campaign. I compared both the cost of the respective campaigns, the revenue generated, the customers acquired and customer retention.</p>
    <p>One of my businesses owns and operates franchised hair salons. We have 15 salons across 2 different brands. The company builds new salons and buys and rehabilitates old salons. One brand is a value focused family salon, the other is a high-end male oriented barbershop. When I open a new barbershop, I set a goal of 350 customers in the first month. Over 12+ months…</p>
    <a class="read-more" href="#">Read more</a>
  </div>
</article>

<article class="post" style="top:1126px;height:429px">
  <div class="post-photo" role="img" aria-label="Bright yellow book cover illustration with a green crocodile" style="background:linear-gradient(180deg,#f2c33a,#f0b92a 75%,#e3b12c)"></div>
  <div class="post-body">
    <h2 class="post-title">Finally dumping Chatterbox on Pocketware – Any recommendations for an SMS app?</h2>
    <div class="post-meta">Posted on March 6, 2014 by Elliot &nbsp;—&nbsp; <span class="comments">Leave a comment</span></div>
    <p>I am embarrassed how long I tried to make Chatterbox on Pocketware work. Chatterbox is Orbitly's default SMS client for Pocketware Marzipan. It combines SMS with Orbitly's chat/video product called Chatterbox. Online, Chatterbox is excellent. It allows you to chat or video with your Orbitly mail contacts, collaboratively work on web documents, have group video chats, etc. On the phone it is painfully slow. Trying to view or send out a text message can take forever. All my business run on Orbitly – email, documents, spreadsheets, chat, video – I am drinking the Sunpop and I love it. It is cheap and works…</p>
    <a class="read-more" href="#">Read more</a>
  </div>
</article>

<article class="post" style="top:1586px;height:303px">
  <div class="post-photo" role="img" aria-label="Traveller standing on a platform as a red and white train blurs past" style="background:linear-gradient(180deg,#6c6f73 0%,#c9cdd1 35%,#e7e2e2 55%,#8f8f8f 100%)"></div>
  <div class="post-body">
    <h2 class="post-title">The Who &amp; The Why</h2>
    <div class="post-meta">Posted on March 6, 2014 by Elliot &nbsp;—&nbsp; <span class="comments">Leave a comment</span></div>
    <p>I started this blog to share much of the knowledge that I have built up during the last 20 years as an entrepreneur. With all of my businesses, I continually run experiments on what works best. I usually summarize my results in little notes to myself – my hope is to share much of that with you. I also hope to learn a lot from the community of entrepreneurs out there.</p>
    <a class="read-more" href="#" style="margin-top:6px">Read more</a>
  </div>
</article>

<nav class="pagination">
  <span class="arrow">&#9664;&#9664;</span>
  <span class="is-current">1</span>
  <span>2</span><span>3</span><span>4</span><span>5</span>
  <span class="arrow">&#9654;&#9654;</span>
</nav>

<div class="divider"></div>

<aside class="widget" style="left:101px">
  <h3>Recent Posts</h3>
  <div class="widget-bar"></div>
  <ul>
    <li>Comparing Direct Mail to Dealsy – By the Numbers</li>
    <li>Finally Dumping Chatterbox on Pocketware – Any Recommendations for an SMS App?</li>
    <li>The Who &amp; The Why</li>
    <li>Donec placerat turpis quam, eu egestas elit venenatis</li>
    <li>Integer malesuada tempor purus</li>
  </ul>
</aside>
<aside class="widget" style="left:444px">
  <h3>Top Posts by Clicks</h3>
  <div class="widget-bar"></div>
  <ul>
    <li>Comparing Direct Mail to Dealsy – By the Numbers</li>
    <li>Finally Dumping Chatterbox on Pocketware – Any Recommendations for an SMS App?</li>
    <li>The Who &amp; The Why</li>
    <li>Donec placerat turpis quam, eu egestas elit venenatis</li>
    <li>Integer malesuada tempor purus</li>
  </ul>
</aside>
<aside class="widget" style="left:787px">
  <h3>Older Posts</h3>
  <div class="widget-bar"></div>
  <ul>
    <li>Comparing Direct Mail to Dealsy – By the Numbers</li>
    <li>Finally Dumping Chatterbox on Pocketware – Any Recommendations for an SMS App?</li>
    <li>The Who &amp; The Why</li>
    <li>Donec placerat turpis quam, eu egestas elit venenatis</li>
    <li>Integer malesuada tempor purus</li>
  </ul>
</aside>

<section class="newsletter">
  <svg width="30" height="22" viewBox="0 0 30 22"><rect x="1.5" y="1.5" width="27" height="19" fill="none" stroke="#fff" stroke-width="2.4"/><path d="M1.5 1.5 15 12 28.5 1.5" fill="none" stroke="#fff" stroke-width="2.4"/></svg>
  <span class="newsletter-label">Newsletter Subscribe</span>
  <div class="newsletter-field">Enter your email ID
    <svg width="26" height="26" viewBox="0 0 26 26"><circle cx="13" cy="13" r="11" fill="#f4f4f4" stroke="#bbb"/><path d="M11 8l5 5-5 5" fill="none" stroke="#999" stroke-width="2"/></svg>
  </div>
  <div class="social-links"><span></span><span></span><span></span><span></span><span></span></div>
</section>

<footer class="site-footer">
  <div class="footer-nav">Home<i>|</i>Small Business<i>|</i>Technology<i>|</i>About Elliot<i>|</i>Contact</div>
  <div class="copyright">Copyright &copy; 2014 &nbsp;Hollow Peak. &nbsp;All rights reserved.</div>
  <a class="to-top" href="#"><svg width="16" height="12" viewBox="0 0 16 12"><path d="M2 10 8 3l6 7" fill="none" stroke="#fff" stroke-width="3"/></svg></a>
</footer>

</body>
</html>
```